Business Card Design Project

The business card is for an educational company that provides personalised tuition to students.

The company logo is in orange and blue (as provided) and should be included in the name card design

The philosophy of the company is to make learning a comfortable experience for student as such design of the namecard should look fresh and has a bit of the 'wow' factor. Some of the namecard design that appeals to me are as uploaded under Sample Design.

The particulars that need to be provided are:
(1): Company Name (Lantern Education)
(1): Name
(2): Educational qualifications which will appear below name
(3): Mobile number
(4): Email address
(5): Website

Industry/Entity Type

Business

Requirements
Must have
• (1): Company Logo

(2): The card background should preferably be coloured both for the front side and back.

(3): The choice of font is important as part of the selection consideration. There is no preferred font that I have selected, designer is free to choose the font that will complement their design.

```html
<!DOCTYPE html>
<html lang="en">
<head>
<meta charset="utf-8">
<title>Lantern Education – Business Card</title>
<link rel="stylesheet" href="https://fonts.googleapis.com/css2?family=Marcellus&display=swap">
<style>
  :root {
    --page-bg: #e6e6e6;
    --orange: #ee7420;
    --orange-deep: #e0661a;
    --blue-light: #3aa3dc;
    --blue: #2d8fcd;
    --blue-deep: #2478b4;
    --ink-dark: #4a4a4a;
    --white: #ffffff;
    --mark-blue: #2f8ccc;
    --mark-orange: #f07c22;
  }
  * { box-sizing: border-box; margin: 0; padding: 0; }
  html, body {
    width: 1200px;
    height: 900px;
    overflow: hidden;
    background: var(--page-bg);
    font-family: "Marcellus", serif;
  }
  .canvas {
    width: 1200px;
    height: 900px;
    display: flex;
    flex-direction: column;
    align-items: center;
    justify-content: center;
    gap: 40px;
  }
  .card {
    width: 680px;
    height: 388px;
    position: relative;
    box-shadow: 0 6px 18px rgba(0,0,0,0.18);
  }

  /* Front side */
  .card--front {
    background: linear-gradient(160deg, var(--orange) 0%, var(--orange-deep) 100%);
  }
  .brand {
    display: flex;
    align-items: center;
    gap: 22px;
  }
  .card--front .brand {
    position: absolute;
    left: 60px;
    top: 150px;
  }
  .brand__square {
    width: 110px;
    height: 100px;
    border-radius: 16px;
    background: var(--mark-blue);
    flex-shrink: 0;
  }
  .brand__name {
    font-size: 52px;
    line-height: 0.95;
    color: var(--white);
  }

  /* Back side */
  .card--back {
    background: radial-gradient(ellipse at 55% 45%, var(--blue-light) 0%, var(--blue) 55%, var(--blue-deep) 100%);
  }
  .card--back .brand {
    position: absolute;
    top: 30px;
    left: 50%;
    transform: translateX(-50%);
    gap: 16px;
  }
  .card--back .brand__square {
    width: 82px;
    height: 76px;
    border-radius: 12px;
    background: var(--mark-orange);
  }
  .card--back .brand__name {
    font-size: 37px;
    color: var(--ink-dark);
  }
  .details {
    position: absolute;
    left: 0;
    right: 0;
    bottom: 40px;
    display: flex;
    justify-content: center;
    align-items: center;
  }
  .person {
    text-align: center;
    padding-right: 46px;
    color: var(--white);
  }
  .person__name {
    font-size: 29px;
    letter-spacing: 1px;
  }
  .person__title {
    font-size: 18px;
    margin-top: 2px;
  }
  .divider {
    width: 1px;
    height: 80px;
    background: rgba(255,255,255,0.6);
  }
  .contact {
    list-style: none;
    padding-left: 34px;
    color: var(--white);
    font-size: 17px;
    line-height: 1.2;
  }
  .contact__item {
    display: flex;
    align-items: center;
    gap: 8px;
  }
  .contact__icon {
    width: 13px;
    height: 13px;
    fill: var(--white);
    flex-shrink: 0;
  }
</style>
</head>
<body>
<main class="canvas">

  <section class="card card--front" aria-label="Card front">
    <div class="brand">
      <span class="brand__square"></span>
      <span class="brand__name">Lantern<br>Education</span>
    </div>
  </section>

  <section class="card card--back" aria-label="Card back">
    <div class="brand">
      <span class="brand__square"></span>
      <span class="brand__name">Lantern<br>Education</span>
    </div>

    <div class="details">
      <div class="person">
        <p class="person__name">JOHN DOE</p>
        <p class="person__title">General manager</p>
      </div>
      <span class="divider"></span>
      <ul class="contact">
        <li class="contact__item">
          <svg class="contact__icon" viewBox="0 0 16 16" aria-hidden="true"><path d="M3.5 1l2.5 3-1.5 1.8c.9 2 2.6 3.7 4.7 4.7L11 9l3 2.5-1.2 2.8C7 14 2 9 1.7 3.2z"/></svg>
          <span>555 010 2468</span>
        </li>
        <li class="contact__item">
          <svg class="contact__icon" viewBox="0 0 16 16" aria-hidden="true"><path d="M4.5 0h7a1 1 0 0 1 1 1v14a1 1 0 0 1-1 1h-7a1 1 0 0 1-1-1V1a1 1 0 0 1 1-1zm.7 2v9h5.6V2zM8 12.3a1 1 0 1 0 0 2 1 1 0 0 0 0-2z"/></svg>
          <span>55501234</span>
        </li>
        <li class="contact__item">
          <svg class="contact__icon" viewBox="0 0 16 16" aria-hidden="true"><path d="M1 3h14v10H1zm1.3 1.2L8 8.5l5.7-4.3z"/></svg>
          <span>info@lanterneducation.com</span>
        </li>
        <li class="contact__item">
          <svg class="contact__icon" viewBox="0 0 16 16" aria-hidden="true"><path d="M8 1a7 7 0 1 0 0 14A7 7 0 0 0 8 1zm0 2a5 5 0 0 1 4.9 4H8.5V5H6.2A5 5 0 0 1 8 3zm-4.9 5H7v3h2.5A5 5 0 0 1 3.1 8z"/></svg>
          <span>www.lanterneducation.com</span>
        </li>
      </ul>
    </div>
  </section>

</main>
</body>
</html>
```